Homemaking training schools needs a Business Card design

Designer, Hello!

No special requirements, good-looking enough.
--------------------------------------------------------------------------

Name: Marcus Dole
Chairman
Tel: 0574-71948263
Mobile: 13857420916
Email: kelvora@mailnest.example
Web: www.prt2019.example
Add: No.258, LanpingJie, BeiyuanQu, Ningbo, Zhejiang

LOGO
Ningbo PRT Homemaking Training School

Target Market(s)

pregnant women, mothers, infants, the elderly and families, including cleaning, cooking, nursing training.

Industry/Entity Type

Business

Contact Information for Business Card

Name: Marcus Dole
Chairman
Tel: 0574-71948263
Mobile: 13857420916
Email: kelvora@mailnest.example
Web: www.prt2019.example

LOGO

Font styles to use
Serif
Sans Serif
Decorative

Requirements
Nice to have
• Feels: clean, specifications, safety, comfort, warmth and happiness.

```html
<!DOCTYPE html>
<html lang="en">
<head>
<meta charset="utf-8">
<title>PeiRuiTang Business Card</title>
<link href="https://fonts.googleapis.com/css2?family=Montserrat:wght@400;500;600;700;800&display=swap" rel="stylesheet">
<style>
  :root {
    --stage: #e9e9ea;
    --card-black: #050505;
    --panel-white: #ffffff;
    --brand-blue: #1c7cc4;
    --brand-pink: #e5078e;
    --text-white: #ffffff;
    --rule-grey: #d8d8d8;
  }
  * { margin: 0; padding: 0; box-sizing: border-box; }
  html, body {
    width: 1200px; height: 900px; overflow: hidden;
    background: var(--stage);
    font-family: "Montserrat", Arial, sans-serif;
  }
  .canvas { position: relative; width: 1200px; height: 900px; }

  .card {
    position: absolute;
    width: 600px; height: 340px;
    background: var(--card-black);
    border-radius: 26px;
    overflow: hidden;
    box-shadow: 0 14px 30px rgba(0,0,0,.28);
  }
  .card--front { left: 90px; top: 110px; }
  .card--back  { left: 510px; top: 460px; }

  /* Front */
  .brand {
    position: absolute; left: 0; right: 0; top: 100px;
    display: flex; flex-direction: column; align-items: center;
  }
  .brand__name {
    font-weight: 600; font-size: 54px; letter-spacing: -0.5px;
    color: var(--brand-blue); line-height: 1;
  }
  .brand__tagline {
    display: flex; align-items: center; gap: 10px;
    margin-top: 14px; color: var(--text-white);
    font-size: 19px; font-weight: 400; letter-spacing: .3px;
  }
  .brand__rule { width: 90px; height: 1px; background: var(--rule-grey); }
  .brand__web {
    margin-top: 12px; font-size: 22px; font-weight: 700;
    color: var(--brand-pink); letter-spacing: .3px;
  }

  /* Back */
  .back-panel { position: absolute; inset: 0; }
  .contact {
    position: absolute; left: 44px; bottom: 34px;
    color: var(--text-white);
  }
  .contact__name {
    font-size: 30px; font-weight: 800; color: var(--brand-pink);
    text-transform: uppercase; letter-spacing: .5px; line-height: 1;
  }
  .contact__title {
    font-size: 14px; font-weight: 700; letter-spacing: .6px;
    margin-top: 6px; margin-bottom: 12px;
  }
  .contact__address { font-size: 15px; font-weight: 500; line-height: 1.35; margin-bottom: 10px; }
  .contact__list { list-style: none; }
  .contact__item {
    display: flex; align-items: center; gap: 10px;
    font-size: 15px; font-weight: 500; line-height: 1.45;
  }
  .contact__icon { width: 13px; height: 13px; flex: none; }
</style>
</head>
<body>
<main class="canvas">

  <section class="card card--front" aria-label="Card front">
    <div class="brand">
      <span class="brand__name">PeiRuiTang</span>
      <div class="brand__tagline">
        <span class="brand__rule"></span>
        <span>Training &amp; Services</span>
        <span class="brand__rule"></span>
      </div>
      <div class="brand__web">www.prt2019.example</div>
    </div>
  </section>

  <section class="card card--back" aria-label="Card back">
    <svg class="back-panel" viewBox="0 0 600 340" preserveAspectRatio="none" aria-hidden="true">
      <path d="M330 0 H600 V340 H470 C420 260 395 170 380 90 C370 45 352 15 330 0 Z" fill="var(--panel-white)"/>
      <path d="M0 220 C14 250 20 290 24 340 H0 Z" fill="var(--panel-white)"/>
    </svg>

    <div class="contact">
      <h1 class="contact__name">Marcus Dole</h1>
      <p class="contact__title">CHAIRMAN</p>
      <p class="contact__address">258, LanpingJie<br>BeiyuanQu, Ningbo, Zhejiang</p>
      <ul class="contact__list">
        <li class="contact__item">
          <svg class="contact__icon" viewBox="0 0 16 16" aria-hidden="true"><path d="M3 1h3l1.5 4-2 1.2a9 9 0 0 0 4.3 4.3L11 8.5l4 1.5v3a2 2 0 0 1-2 2A12 12 0 0 1 1 3a2 2 0 0 1 2-2z" fill="var(--brand-pink)"/></svg>
          <span>0574-71948263</span>
        </li>
        <li class="contact__item">
          <svg class="contact__icon" viewBox="0 0 16 16" aria-hidden="true"><rect x="3.5" y="1" width="9" height="14" rx="1.6" fill="none" stroke="var(--brand-pink)" stroke-width="1.8"/><circle cx="8" cy="12.3" r="1" fill="var(--brand-pink)"/></svg>
          <span>13857420916</span>
        </li>
        <li class="contact__item">
          <svg class="contact__icon" viewBox="0 0 16 16" aria-hidden="true"><rect x="1" y="3" width="14" height="10" rx="1" fill="none" stroke="var(--brand-pink)" stroke-width="1.8"/><path d="M1.5 3.5 8 9l6.5-5.5" fill="none" stroke="var(--brand-pink)" stroke-width="1.6"/></svg>
          <span>kelvora@mailnest.example</span>
        </li>
        <li class="contact__item">
          <svg class="contact__icon" viewBox="0 0 16 16" aria-hidden="true"><circle cx="8" cy="8" r="6.5" fill="none" stroke="var(--brand-pink)" stroke-width="1.6"/><ellipse cx="8" cy="8" rx="2.8" ry="6.5" fill="none" stroke="var(--brand-pink)" stroke-width="1.3"/><path d="M1.5 8h13" stroke="var(--brand-pink)" stroke-width="1.3"/></svg>
          <span>www.prt2019.example</span>
        </li>
      </ul>
    </div>
  </section>

</main>
</body>
</html>
```